Business card for a new cabinet shop company named Veloran Cabinets for high end cabinets

Design a business card, thinking dark rich green with colours to speak of high end luxury ie; cream, gold, black possibly

Mitchell Tarrowby
Director Craftsman
Email: info@veloranjoinery-example.com.au
Instagram : @veloran.cabinets

```html
<!DOCTYPE html>
<html lang="en">
<head>
<meta charset="UTF-8">
<title>Veloran Cabinets — Business Card</title>
<link rel="stylesheet" href="https://fonts.googleapis.com/css2?family=Montserrat:wght@400;700&family=Poppins:wght@500&display=swap">
<style>
  :root {
    --backdrop: #9a9a9a;
    --card-green: #06402b;
    --gold: #c8a96a;
    --cream: #ffffff;
  }
  html, body {
    margin: 0;
    padding: 0;
    width: 1200px;
    height: 1059px;
    overflow: hidden;
    background: var(--backdrop);
  }
  .canvas {
    position: relative;
    width: 1200px;
    height: 1059px;
  }
  .card {
    position: absolute;
    left: 252px;
    width: 700px;
    height: 400px;
    border-radius: 30px;
    background: var(--card-green);
    overflow: hidden;
  }
  .card--front { top: 86px; }
  .card--back { top: 568px; }

  .wordmark {
    font-family: "Poppins", sans-serif;
    font-weight: 500;
    color: var(--gold);
    line-height: 1.05;
    margin: 0;
  }
  .card--front .wordmark {
    position: absolute;
    right: 46px;
    top: 52px;
    font-size: 42px;
    text-align: right;
  }
  .card--back .wordmark {
    position: absolute;
    left: 0;
    right: 0;
    top: 50%;
    transform: translateY(-50%);
    font-size: 58px;
    text-align: center;
  }

  .person {
    position: absolute;
    left: 53px;
    top: 226px;
  }
  .person__name {
    margin: 0;
    font-family: "Montserrat", sans-serif;
    font-weight: 700;
    font-size: 33px;
    color: var(--gold);
    letter-spacing: 0.2px;
  }
  .person__title {
    margin: 6px 0 0 2px;
    font-family: "Montserrat", sans-serif;
    font-weight: 400;
    font-size: 19px;
    color: var(--cream);
  }
  .divider {
    position: absolute;
    left: 53px;
    right: 47px;
    top: 314px;
    height: 1.5px;
    background: var(--cream);
  }
  .contacts {
    position: absolute;
    left: 53px;
    right: 47px;
    top: 336px;
    display: flex;
    justify-content: space-between;
    align-items: center;
    font-family: "Montserrat", sans-serif;
    font-weight: 400;
    font-size: 18px;
    color: var(--cream);
  }
  .contact {
    display: flex;
    align-items: center;
    gap: 8px;
  }
  .contact__icon { display: block; }
  .contact__dot {
    width: 13px;
    height: 13px;
    border-radius: 50%;
    border: 2px solid var(--gold);
    box-sizing: border-box;
  }
</style>
</head>
<body>
<main class="canvas">
  <section class="card card--front" aria-label="Card front">
    <p class="wordmark">Veloran<br>Cabinets</p>

    <div class="person">
      <h1 class="person__name">Mitchell Tarrowby</h1>
      <p class="person__title">Director Craftsman</p>
    </div>

    <div class="divider"></div>

    <div class="contacts">
      <div class="contact contact--email">
        <svg class="contact__icon" width="18" height="13" viewBox="0 0 18 13" aria-hidden="true">
          <rect x="0" y="0" width="18" height="13" fill="var(--gold)"/>
          <path d="M0 0 L9 7 L18 0" fill="none" stroke="var(--card-green)" stroke-width="1.6"/>
        </svg>
        <span>info@veloranjoinery-example.com.au</span>
      </div>
      <div class="contact contact--social">
        <span class="contact__dot" aria-hidden="true"></span>
        <span>@veloran.cabinets</span>
      </div>
    </div>
  </section>

  <section class="card card--back" aria-label="Card back">
    <p class="wordmark">Veloran<br>Cabinets</p>
  </section>
</main>
</body>
</html>
```